Stationery Design Project for Marketing Consultancy

I have started a new consultancy business and require the following elements to be designed using existing logo:
• Business card
• Letterhead
• Envelope (DL, C4, C5)
• Microsoft word template for report writing
• A4 Presentation Folder
• Powerpoint template
COPY FOR FRONT AND BACK OF BUSINESS CARD
logo
'Measurable Marketing. Epic Results' slogan (but no need to use existing lockup with logo)
name, B Bus. Mktg, Grad Dip Digital Mktg, CPM (post nominal abbreviations in smaller font)
mobile: 04XX-XXX-XXX (I will give details to the winner to add)
website: www.tolvarin.com.au
email: info@tolvarin.com.au
COPY FOR LETTERHEAD
Logo
Company Name
Please, submit your designs that include business card, letterhead and envelope. Once selected the winner will be asked to complete the project by creating the rest of the artwork.
FINAL FILES
Print ready files to be supplied as well as Indesign files so that minor amends can be made if necessary in future.
• Layered vectors in EPS & PDF
• Screen quality JPEG & PNGs
ABOUT THE BUSINESS: TOLVARIN
I work with clients to understand their business challenges, developing and executing measurable marketing strategies tied to key business metrics. Services include:
Services include:
• Business planning and business development
• Marketing and brand strategy
• Insight-driven integrated campaigns
• Loyalty programs and retention marketing
• Marketing automation
• Direct marketing (traditional and digital)
• Content strategy and development
Hi everyone,
Target Market(s)
Corporate decision makers (heads of marketing, general managers etc) and small to medium sized business owners. Predominately male aged 35+
Industry/Entity Type
Marketing
Requirements
Must have
- BRAND PERSONALITY
The successful design will communicate brand personality. I am a professional, results-driven entrepreneur, but want to show off my creative flair.
MEMORABILITY
Looking for a unique and eye-catching design. Am considering special printing effects (die cuts, letterpress, interactive elements, embossing, foiling etc) or a striking minimalist approach.
Nice to have
- I have a mission that could be incorporated on reverse if room -
Turning insights into actions & passion into profit.
Should not have
- Use of pink or green.

```html
<!DOCTYPE html>
<html lang="en">
<head>
<meta charset="utf-8">
<title>Tolvarin Business Card</title>
<link href="https://fonts.googleapis.com/css2?family=Open+Sans:wght@400;600;700&display=swap" rel="stylesheet">
<style>
  :root {
    --page-bg: #e4e2df;
    --card-top: #3b3b3b;
    --card-bottom: #161616;
    --silver: #d9d9d9;
    --silver-dim: #a9a9a9;
    --text-light: #f2f2f2;
  }
  * { margin: 0; padding: 0; box-sizing: border-box; }
  html, body {
    width: 1200px; height: 818px; overflow: hidden;
    background: var(--page-bg);
    font-family: "Open Sans", Arial, sans-serif;
  }
  .stage {
    position: relative; width: 1200px; height: 818px;
    display: flex; align-items: center; justify-content: center; gap: 80px;
  }
  .card {
    position: relative; width: 480px; height: 322px;
    background: radial-gradient(ellipse at 35% 15%, var(--card-top), var(--card-bottom) 80%);
    box-shadow: 0 6px 18px rgba(0,0,0,.25);
    color: var(--text-light);
  }
  /* Front */
  .card-front { display: flex; flex-direction: column; align-items: center; justify-content: center; }
  .brand { display: flex; flex-direction: column; align-items: center; gap: 14px; }
  .brand-dot { width: 64px; height: 64px; border-radius: 50%; background: var(--silver); }
  .brand-name {
    font-size: 42px; font-weight: 600; letter-spacing: 1px; line-height: 1; color: var(--silver);
  }
  .slogan {
    margin-top: 8px; font-size: 11.5px; letter-spacing: .4px; color: var(--silver-dim);
    text-transform: uppercase;
  }
  /* Back */
  .contact { position: absolute; left: 118px; top: 116px; }
  .contact-name { font-size: 20px; font-weight: 700; margin-bottom: 16px; }
  .contact-line { font-size: 14.5px; line-height: 21px; }
  .contact-web { font-size: 18px; font-weight: 700; margin-top: 8px; }
  .mini-brand {
    position: absolute; right: 26px; top: 40px; text-align: center;
    display: flex; flex-direction: column; align-items: center;
  }
  .mini-dot { width: 20px; height: 20px; border-radius: 50%; background: var(--silver); margin-bottom: 5px; }
  .mini-name { font-size: 16px; font-weight: 600; color: var(--silver); letter-spacing: .5px; }
  .mini-slogan { font-size: 6px; color: var(--silver-dim); text-transform: uppercase; }
</style>
</head>
<body>
  <main class="stage">
    <section class="card card-front">
      <div class="brand">
        <span class="brand-dot"></span>
        <span class="brand-name">TOLVARIN</span>
      </div>
      <p class="slogan">Clear Metrics. Bold Growth.</p>
    </section>

    <section class="card card-back">
      <div class="contact">
        <p class="contact-name">Company Name</p>
        <p class="contact-line">M xxx xxx xxxx</p>
        <p class="contact-line">E info@tolvarin.com.au</p>
        <p class="contact-web">www.tolvarin.com.au</p>
      </div>
      <div class="mini-brand">
        <span class="mini-dot"></span>
        <span class="mini-name">TOLVARIN</span>
        <span class="mini-slogan">Clear Metrics. Bold Growth.</span>
      </div>
    </section>
  </main>
</body>
</html>
```